Business Card Design

New business card design

Target Market(s)

Residential & Commercial Property Managers

Industry/Entity Type

Plumbing Services

Contact Information for Business Card

Name - Rowan Keddle, title - Director, Phone Number - 0431 286 517, email - rowan@tbk-plumbing.com.au, Company ABN - 73 215 904 386,

Font styles to use
Sans Serif

Colors
0054AA
0677BA
7BADD7
CADEEF
E8F1F8

```html
<!DOCTYPE html>
<html lang="en">
<head>
<meta charset="utf-8">
<title>TBK Plumbing – Business Card</title>
<link href="https://fonts.googleapis.com/css2?family=Montserrat:ital,wght@0,400;0,600;0,700;1,400&display=swap" rel="stylesheet">
<style>
  :root {
    --stage: #e9edf1;
    --card: #ffffff;
    --brand-blue: #2ca6df;
    --ink: #1c252d;
    --on-blue: #ffffff;
    --shadow: rgba(20, 35, 50, 0.18);
  }
  * { margin: 0; padding: 0; box-sizing: border-box; }
  html, body {
    width: 1200px; height: 900px; overflow: hidden;
    background: var(--stage);
    font-family: "Montserrat", Arial, sans-serif;
  }
  .stage {
    width: 1200px; height: 900px;
    display: flex; flex-direction: column; align-items: center; justify-content: center;
    gap: 40px;
  }
  .card {
    position: relative;
    width: 620px; height: 380px;
    background: var(--card);
    border-radius: 34px;
    overflow: hidden;
    box-shadow: 0 10px 30px var(--shadow);
  }
  .brand {
    display: flex; align-items: center; gap: 12px;
    color: var(--ink);
    font-weight: 600;
    white-space: nowrap;
  }
  .brand-dot {
    width: 12px; height: 12px; border-radius: 50%;
    background: var(--brand-blue);
    flex: none;
  }
  .card-back { display: flex; align-items: center; justify-content: center; }
  .card-back .brand { font-size: 52px; letter-spacing: 1px; }
  .card-back .brand-dot { width: 14px; height: 14px; }

  .front-shape { position: absolute; inset: 0; width: 100%; height: 100%; }
  .front-shape path { fill: var(--brand-blue); }

  .holder {
    position: absolute; left: 38px; top: 30px;
    color: var(--on-blue);
  }
  .holder-name { font-weight: 700; font-size: 25px; }
  .holder-title { font-style: italic; font-size: 16px; margin-top: 2px; }

  .contact {
    position: absolute; left: 38px; bottom: 28px;
    color: var(--on-blue);
    font-size: 17px; line-height: 1.45;
  }
  .contact-abn { margin-bottom: 8px; }
  .contact-line { display: flex; align-items: center; gap: 10px; }
  .contact-line svg { width: 17px; height: 17px; flex: none; }
  .contact-line svg * { fill: none; stroke: var(--on-blue); stroke-width: 1.8; stroke-linecap: round; stroke-linejoin: round; }

  .front-brand-area {
    position: absolute; left: 300px; right: 24px; top: 140px; height: 60px;
    display: flex; align-items: center; justify-content: center;
  }
  .card-front .brand { font-size: 30px; }
</style>
</head>
<body>
<main class="stage">
  <section class="card card-back" aria-label="Business card back">
    <div class="brand"><span class="brand-dot"></span><span>TBK Plumbing</span></div>
  </section>

  <section class="card card-front" aria-label="Business card front">
    <svg class="front-shape" viewBox="0 0 620 380" preserveAspectRatio="none" aria-hidden="true">
      <path d="M0,0 H370 C290,18 300,166 215,166 H0 Z"/>
      <path d="M0,178 H225 C320,178 305,380 405,380 H0 Z"/>
    </svg>

    <div class="holder">
      <p class="holder-name">Rowan Keddle</p>
      <p class="holder-title">Director</p>
    </div>

    <div class="contact">
      <p class="contact-abn">Company ABN -<br>73 215 904 386</p>
      <p class="contact-line">
        <svg viewBox="0 0 24 24" aria-hidden="true"><path d="M5 3h4l2 5-2.5 1.5a11 11 0 0 0 6 6L16 13l5 2v4a2 2 0 0 1-2 2A16 16 0 0 1 3 5a2 2 0 0 1 2-2z"/></svg>
        <span>0431 286 517</span>
      </p>
      <p class="contact-line">
        <svg viewBox="0 0 24 24" aria-hidden="true"><rect x="3" y="5" width="18" height="14" rx="2"/><path d="M3 7l9 6 9-6"/></svg>
        <span>rowan@tbk-plumbing.com.au</span>
      </p>
    </div>

    <div class="front-brand-area">
      <div class="brand"><span class="brand-dot"></span><span>TBK Plumbing</span></div>
    </div>
  </section>
</main>
</body>
</html>
```